Laser Tattoo Removal Business Cards

We are looking for a professional business card design for a laser tattoo removal business. Ideally looking for a black business card design. The name of the business is Brightline Tattoo Removal. We place our cards at local tattoo shops so we ideally are looking for something trendy/edgy to draw both male and female clientele in.

Target Market(s)

Male/Female ages 18-60

Contact Information for Business Card

black background ideally.. hoping to stay within greys, whites and black

Font styles to use
Serif
Sans Serif

Colors
121212
a9a9a9
5c5c5c
f5f5f5
ffffff
7f7f7f
606060
848484
9d9d9d

Requirements
Must have
• Employee Info:
• Melissa Thornbury
• Chief Executive Offer
• m: 919.537.2846
• w: 919.362.4178
• f: 919.685.3907
• mthornbury@brightlinetattooremoval.example
• Address:
• 4615 Oakmere Pkwy, Suite 210
• Raleigh, NC 27654
• Website:
• www.brightlinetattooremoval.example
Nice to have
• Myabe business name on back or logo on back and employee info on the front

```html
<!DOCTYPE html>
<html lang="en">
<head>
<meta charset="utf-8">
<title>Brightline Tattoo Removal – Business Cards</title>
<link rel="stylesheet" href="https://fonts.googleapis.com/css2?family=Roboto:wght@400;500;700&display=swap">
<style>
  :root {
    --backdrop: #2f2b28;
    --card: #121212;
    --white: #ffffff;
    --soft-white: #f5f5f5;
    --grey-light: #a9a9a9;
    --grey-mid: #7f7f7f;
    --grey-dark: #5c5c5c;
  }
  * { box-sizing: border-box; margin: 0; padding: 0; }
  html, body {
    width: 1200px; height: 769px; overflow: hidden;
    background: var(--backdrop);
    font-family: "Roboto", Arial, sans-serif;
  }
  .stage { position: relative; width: 1200px; height: 769px; }
  .card {
    position: absolute; top: 236px;
    width: 520px; height: 297px;
    background: var(--card);
    border-radius: 3px;
    box-shadow: 0 14px 30px rgba(0,0,0,.45);
    color: var(--white);
  }
  .card--front { left: 60px; }
  .card--back  { left: 620px; }

  .brand {
    display: flex; align-items: center; gap: 10px;
    font-size: 22px; font-weight: 500; letter-spacing: 1.5px;
    color: var(--white); white-space: nowrap;
  }
  .brand__mark { width: 10px; height: 10px; background: var(--white); }
  .card--front .brand { position: absolute; top: 52px; right: 34px; font-size: 19px; }
  .card--back .brand { position: absolute; top: 112px; left: 0; right: 0; justify-content: center; color: var(--soft-white); }
  .card--back .brand .brand__mark { background: var(--soft-white); }

  .rule { position: absolute; height: 1px; background: var(--grey-mid); }
  .card--front .rule { top: 90px; right: 34px; width: 270px; }
  .card--back .rule { top: 152px; left: 160px; width: 200px; }

  .website {
    position: absolute; top: 182px; left: 0; right: 0;
    text-align: center; font-size: 11px; letter-spacing: 3px;
    color: var(--soft-white);
  }

  .contact { position: absolute; left: 30px; bottom: 22px; }
  .contact__name { font-size: 17px; font-weight: 700; letter-spacing: .3px; }
  .contact__title { font-size: 13px; font-weight: 500; margin-bottom: 6px; }
  .contact__address { font-size: 12.5px; line-height: 1.3; margin-bottom: 6px; color: var(--soft-white); }
  .contact__list { list-style: none; font-size: 12.5px; color: var(--soft-white); }
  .contact__list li { display: flex; align-items: center; gap: 9px; height: 17px; }
  .contact__list svg { width: 11px; height: 11px; fill: var(--white); flex: none; }
</style>
</head>
<body>
<main class="stage">
  <section class="card card--front">
    <div class="brand"><span class="brand__mark"></span>Brightline Tattoo Removal</div>
    <div class="rule"></div>
    <div class="contact">
      <p class="contact__name">MELISSA THORNBURY</p>
      <p class="contact__title">Chief Executive Offer</p>
      <p class="contact__address">4615 Oakmere Pkwy, Suite 210<br>Raleigh, NC 27654</p>
      <ul class="contact__list">
        <li><svg viewBox="0 0 12 12"><path d="M2.5 1l2 2.2-1 1.3c.8 1.6 2 2.8 3.5 3.6l1.3-1L11 9.2 9.6 11C5 10.5 1.5 7 1 2.4z"/></svg>919.362.4178</li>
        <li><svg viewBox="0 0 12 12"><path d="M3 0h6v12H3zM4 1.5v8h4v-8z"/></svg>919.537.2846</li>
        <li><svg viewBox="0 0 12 12"><path d="M3 0h6v3H3zM1 4h10v5H9v3H3V9H1zM4 8v3h4V8z"/></svg>919.685.3907</li>
        <li><svg viewBox="0 0 12 12"><path d="M0 2h12v1L6 7 0 3zM0 4.5l6 4 6-4V10H0z"/></svg>mthornbury@brightlinetattooremoval.example</li>
        <li><svg viewBox="0 0 12 12"><circle cx="6" cy="6" r="5.5"/></svg>www.brightlinetattooremoval.example</li>
      </ul>
    </div>
  </section>

  <section class="card card--back">
    <div class="brand"><span class="brand__mark"></span>Brightline Tattoo Removal</div>
    <div class="rule"></div>
    <p class="website">www.brightlinetattooremoval.example</p>
  </section>
</main>
</body>
</html>
```